Website Redesign for Non-Profit Ministry & Church

NOTE: Please do not contact me privately — all private inquiries will be ignored.

Individuals seeking spiritual healing, community connection, ministry support and journal-based encounters.

Description of What’s Needed

We need a clean, fresh, inviting website that encourages engagement and connection. The site should feel warm and accessible, draw people in, and clearly present who we are, what we offer, and how visitors can participate. The layout should be straightforward, with well-structured pages (no overlapping objects, minimal layering complexity) and easy to navigate. Use only Google Fonts. All stock photos must be sourced from royalty-free sites and include proper attribution. We will not include a search feature.

Pages to Create
1. Home Page – impactful hero area, clear call-to-action, visual story of ministry, giving/gathering invitation.
2. About Us – vision, mission, leadership, testimonies, history.
3. Meetings & Events – upcoming gatherings, schedule, how to attend, sign-up or interest form.
4. Encounter: “Lanterns by the River” (book) – dedicated page for the book, overview, purchase link or details, journal prompts, imagery.
5. Healing Rooms / Ministry – explain ministry offerings, invite participation, testimonials or case-studies.
6. Live Stream & Links Page – page listing links for YouTube live stream, other platforms, archive links; simple layout.

Colour & Branding

Use colours that blend with our existing logo (attached). The palette should feel contemporary, welcoming, and aligned with ministry themes of restoration, healing and love. Ensure text, button and link colours maintain good contrast for accessibility.

Existing Content & Reference

Please gather available content from our current website in the attachment here for text, images and structure for reuse.

Imagery Guidelines

– Use original photos from our Facebook page or Google Location listing for building or people images when available.
– If generic images are used, ensure they depict appropriate ministry-related buildings or people (community, warm gathering) — avoid generic unrelated stock imagery.
– All photos must be royalty-free or have proper licensing and attribution.
– No overlapping objects or visual clutter; clean layouts with defined sections.

Additional Notes

– Integration: We currently utilise MailChimp for email communication; the design should include a connection/invite to subscribe (via MailChimp) but no blog page is required at this time.
– Payment/Giving: We accept PayPal and already have a giving portal; include clear donation/give buttons or calls-to-action linking to existing giving systems.
– No search function to be included.
– Layouts should avoid complex layering or overlapping elements—designers should work with distinct content blocks, clear visual hierarchy, and straightforward mobile-friendly structure.

Target Market(s)

Industry/Entity Type

Church/Religious institution

Number of Pages Required

5+ page

Requirements
Should not have
• search bar

```html
<!DOCTYPE html>
<html lang="en">
<head>
<meta charset="utf-8">
<title>Mended, Cherished, Whole — Home</title>
<link href="https://fonts.googleapis.com/css2?family=Lexend:wght@500;600;700;800&family=Mulish:wght@400;600;700;800&display=swap" rel="stylesheet">
<style>
:root{
  --teal:#1a9a86;
  --teal-dark:#13806f;
  --purple:#4b1a80;
  --forest:#0e5a3a;
  --ink:#1b1b1b;
  --text:#333;
  --muted:#555;
  --aqua:#e5f8f8;
  --line:#d9d9d9;
  --white:#fff;
}
*{box-sizing:border-box;margin:0;padding:0}
html,body{width:1200px;height:3783px;overflow:hidden}
body{font-family:'Mulish',sans-serif;color:var(--text);background:var(--white);position:relative}
.abs{position:absolute}
h1,h2,h3{font-family:'Lexend',sans-serif}
.btn{position:absolute;display:flex;align-items:center;justify-content:center;background:var(--teal);color:var(--white);font-family:'Lexend',sans-serif;font-weight:600;font-size:13px;letter-spacing:.3px;border-radius:22px;text-transform:uppercase}

/* header */
.site-header{position:absolute;left:0;top:0;width:1200px;height:133px;background:var(--white)}
.brand{position:absolute;display:flex;align-items:center;gap:10px}
.brand-dot{width:34px;height:34px;border-radius:50%;background:var(--teal)}
.brand-name{font-family:'Mulish',sans-serif;font-weight:800;line-height:1.02}
.header-brand{left:154px;top:24px}
.header-brand .brand-name{color:var(--forest);font-size:25px}
.follow-label{left:543px;top:33px;font-size:14px;color:var(--muted)}
.social{position:absolute;width:33px;height:33px;border-radius:50%;border:1.5px solid #9a9a9a}
.phone-btn{left:761px;top:23px;width:151px;height:39px;border:2px solid var(--teal);background:var(--white);color:var(--teal);font-family:'Mulish',sans-serif;font-size:13px;gap:7px}
.contact-btn{left:922px;top:23px;width:128px;height:39px;font-size:12px;font-weight:500}
.main-nav{position:absolute;left:407px;top:78px;display:flex;align-items:center;font-size:12.5px;color:#222;text-transform:uppercase}
.main-nav span{margin-right:26px}
.main-nav .active{background:var(--purple);color:var(--white);padding:8px 13px;border-radius:4px;margin-right:20px}

/* hero */
.hero{position:absolute;left:0;top:133px;width:1200px;height:532px;background:linear-gradient(180deg,#6d93c9 0%,#a9c3e3 38%,#c9d7e4 52%,#6f9a4b 68%,#5b8a38 100%)}
.hero-title{left:0;width:1200px;top:42px;text-align:center;color:var(--white);font-size:53px;font-weight:700}
.hero-sub{left:0;width:1200px;top:116px;text-align:center;color:var(--white);font-size:21px;line-height:34px}
.hero .btn{top:206px;height:43px;font-size:13.5px}

/* welcome */
.welcome{position:absolute;left:0;top:665px;width:1200px;height:539px}
.welcome-kicker{left:151px;top:50px;font-size:25px;font-weight:600;color:var(--ink)}
.welcome-title{left:151px;top:86px;width:420px;font-size:28px;font-weight:700;color:var(--purple);white-space:nowrap;line-height:40px}
.welcome-rule{left:153px;top:136px;width:47px;height:3px;background:var(--purple)}
.welcome-copy{left:153px;top:168px;width:395px;font-size:15px;line-height:22.5px;color:#2a2a2a}
.welcome-copy p{margin-bottom:15px}
.welcome .btn{left:153px;top:432px;width:130px;height:43px}
.welcome-photo{left:592px;top:58px;width:455px;height:426px;border-radius:10px;background:linear-gradient(135deg,#d9dde4 0%,#c6cad6 45%,#4a4f7a 75%,#2d2b5c 100%)}

/* mission & vision */
.purpose{position:absolute;left:0;top:1204px;width:1200px;height:369px;background:var(--aqua)}
.purpose-card{position:absolute;top:55px;width:431px;height:263px;border:1.5px solid var(--teal);border-radius:8px;text-align:center}
.purpose-card svg{margin-top:26px}
.purpose-card h2{font-size:35px;font-weight:700;color:var(--forest);margin-top:8px}
.purpose-card p{font-size:14.5px;line-height:22.5px;color:#333;width:340px;margin:14px auto 0}

/* events */
.events{position:absolute;left:0;top:1573px;width:1200px;height:476px}
.section-title{left:0;width:1200px;text-align:center;font-size:35px;font-weight:700;color:var(--ink)}
.section-rule{left:576px;width:47px;height:3px;background:var(--ink)}
.event-row{position:absolute;left:151px;top:169px;display:flex;gap:14px}
.event-card{width:214px;height:246px;border-radius:8px;background:var(--white);box-shadow:0 0 0 1px #eee,0 3px 10px rgba(0,0,0,.12);padding:25px 22px}
.event-card h3{font-family:'Lexend',sans-serif;font-size:16px;font-weight:600;line-height:20px;color:var(--ink);height:40px}
.event-by{font-size:12.5px;line-height:19px;color:#333;margin-top:12px}
.event-date{margin-top:18px;width:103px;height:88px;background:var(--aqua);border-radius:6px;padding:12px 0 0 20px;color:var(--ink)}
.event-date .day{font-size:12px}
.event-date .date{font-family:'Lexend',sans-serif;font-size:17px;font-weight:700;margin:2px 0}
.event-date .time{font-size:12px}
.chev{position:absolute}

/* invitation */
.invite{position:absolute;left:0;top:2049px;width:1200px;height:504px;background:radial-gradient(ellipse at 50% 45%,#3f4660 0%,#2b3046 45%,#1d2030 100%)}
.invite-title{left:0;width:1200px;top:58px;text-align:center;color:var(--white);font-size:51px;font-weight:700}
.invite-copy{left:0;width:1200px;top:119px;text-align:center;color:var(--white);font-size:18.5px;font-weight:600;line-height:28px}
.invite .btn{left:514px;top:198px;width:181px;height:42px}

/* testimonials */
.testimonials{position:absolute;left:0;top:2553px;width:1200px;height:477px}
.quote-row{position:absolute;left:151px;top:160px;display:flex;gap:20px}
.quote-card{position:relative;width:286px;height:253px;border:1.5px solid #d6d6d6;border-radius:8px;padding:28px 34px 0 34px}
.quote-card p{font-size:14.5px;line-height:21.2px;color:#333}
.quote-author{position:absolute;left:34px;top:182px;display:flex;align-items:center;gap:13px}
.avatar{width:36px;height:36px;border-radius:50%;background:#8b7a74}
.quote-author b{display:block;font-size:14px;color:var(--ink)}
.quote-author span{font-size:12.5px;color:#555}

/* newsletter */
.newsletter{position:absolute;left:0;top:3030px;width:1200px;height:423px;background:var(--aqua)}
.newsletter-photo{left:0;top:0;width:564px;height:423px;background:linear-gradient(180deg,#6b5238 0%,#4a3a2e 30%,#2d2f3f 60%,#1c1d2b 100%)}
.newsletter-title{left:620px;top:58px;font-size:36px;font-weight:700;color:var(--ink)}
.newsletter-copy{left:620px;top:110px;width:360px;font-size:17px;line-height:27px;color:#333}
.field{position:absolute;height:42px;border:1.5px solid #cfcfcf;border-radius:21px;background:var(--white);font-size:11.5px;color:#333;padding:13px 0 0 20px}
.subscribe{left:618px;top:313px;width:432px;height:53px;border-radius:10px;font-size:24px;font-weight:700;text-transform:none;letter-spacing:0}

/* footer */
.site-footer{position:absolute;left:0;top:3453px;width:1200px;height:330px;background:var(--purple);color:var(--white)}
.footer-brand{left:151px;top:55px}
.footer-brand .brand-name{color:var(--white);font-size:36px}
.footer-brand .brand-dot{width:44px;height:44px;background:var(--white)}
.footer-head{font-family:'Lexend',sans-serif;font-size:13px;font-weight:700;letter-spacing:.4px}
.footer-col{position:absolute;top:47px;font-size:12px;line-height:21px}
.footer-col ul{list-style:none;margin-top:8px}
.contact-line{display:flex;gap:10px;margin-top:8px;line-height:18px}
.contact-line svg{flex:none;margin-top:2px}
.footer-social{position:absolute;width:33px;height:33px;border-radius:50%;border:1.5px solid var(--white)}
.footer-rule{left:151px;top:241px;width:898px;height:1px;background:rgba(255,255,255,.55)}
.copyright{left:0;width:1200px;top:278px;text-align:center;font-size:12px;color:#e4d9f0}
</style>
</head>
<body>

<header class="site-header">
  <div class="brand header-brand">
    <div class="brand-dot"></div>
    <div class="brand-name">Mended<br>Cherished<br>Whole</div>
  </div>
  <div class="abs follow-label">Follow us</div>
  <div class="social" style="left:623px;top:26px" aria-label="Social profile"></div>
  <div class="social" style="left:666px;top:26px" aria-label="Social profile"></div>
  <div class="social" style="left:708px;top:26px" aria-label="Social profile"></div>
  <div class="btn phone-btn">
    <svg width="14" height="14" viewBox="0 0 24 24"><path d="M6.6 10.8a15 15 0 0 0 6.6 6.6l2.2-2.2a1 1 0 0 1 1-.25 11.4 11.4 0 0 0 3.6.57 1 1 0 0 1 1 1V20a1 1 0 0 1-1 1A17 17 0 0 1 3 4a1 1 0 0 1 1-1h3.5a1 1 0 0 1 1 1c0 1.25.2 2.45.57 3.6a1 1 0 0 1-.25 1z" fill="#1a9a86"/></svg>
    555-201-4480
  </div>
  <div class="btn contact-btn">Contact Us</div>
  <nav class="main-nav">
    <span class="active">Home</span>
    <span>About Us</span>
    <span>Meetings &amp; Events</span>
    <span>Encounter</span>
    <span>Healing Rooms</span>
    <span>Live Stream</span>
  </nav>
</header>

<section class="hero" role="img" aria-label="Photo of a small red-brick country church under a blue sky beside green fields">
  <h1 class="abs hero-title">Mended, Cherished, Whole</h1>
  <p class="abs hero-sub">Activating and proclaiming the Father’s love<br>through Jesus, guided by the Holy Spirit.</p>
  <div class="btn" style="left:423px;width:181px">Get Involved</div>
  <div class="btn" style="left:615px;width:182px">Connect With Us</div>
</section>

<section class="welcome">
  <h2 class="abs welcome-kicker">Welcome to</h2>
  <h2 class="abs welcome-title">Mended, Cherished, Whole</h2>
  <div class="abs welcome-rule"></div>
  <div class="abs welcome-copy">
    <p>Daniel and Clara Jean have been married for 42 years and have two adult children. They both grew up in southern Illinois.</p>
    <p>Their desire is to share the love of Christ with others. They have numerous stories to share about the many ways they have seen God move in their lives as well as the lives of others.</p>
    <p>They believe in the manifestation of God’s power through signs and wonders.</p>
  </div>
  <div class="btn">Read More</div>
  <div class="abs welcome-photo" role="img" aria-label="Photo of the ministry's founding couple standing beside a stained-glass window"></div>
</section>

<section class="purpose">
  <div class="purpose-card" style="left:151px">
    <svg width="72" height="72" viewBox="0 0 72 72" aria-hidden="true">
      <circle cx="32" cy="40" r="25" fill="none" stroke="#1a9a86" stroke-width="6"/>
      <circle cx="32" cy="40" r="14" fill="none" stroke="#1a9a86" stroke-width="6"/>
      <circle cx="32" cy="40" r="4" fill="#1a9a86"/>
      <path d="M34 38 L58 14" stroke="#1a9a86" stroke-width="5" stroke-linecap="round"/>
      <path d="M52 8 L58 14 L66 14 L60 20 L54 20 Z" fill="#1a9a86"/>
    </svg>
    <h2>Mission</h2>
    <p>Honoring God’s presence by loving the broken, saving the lost, and healing the hurting through the demonstration of His love and power.</p>
  </div>
  <div class="purpose-card" style="left:617px">
    <svg width="80" height="72" viewBox="0 0 80 72" aria-hidden="true">
      <path d="M4 38 Q40 2 76 38 Q40 74 4 38 Z" fill="none" stroke="#1a9a86" stroke-width="5"/>
      <circle cx="40" cy="38" r="13" fill="none" stroke="#1a9a86" stroke-width="5"/>
      <path d="M33 42 L38 36 L42 40 L47 33" fill="none" stroke="#1a9a86" stroke-width="3"/>
      <path d="M40 4v8M22 10l4 6M58 10l-4 6M10 20l5 4M70 20l-5 4" stroke="#1a9a86" stroke-width="3.5" stroke-linecap="round"/>
    </svg>
    <h2>Vision</h2>
    <p>Mended, Cherished, Whole exists to activate, proclaim, and teach the Father’s love through Jesus, guided by the Holy Spirit.</p>
  </div>
</section>

<section class="events">
  <h2 class="abs section-title" style="top:44px">Upcoming Events</h2>
  <div class="abs section-rule" style="top:119px"></div>
  <svg class="chev" style="left:72px;top:268px" width="26" height="44" viewBox="0 0 26 44"><path d="M22 2 L4 22 L22 42" fill="none" stroke="#999" stroke-width="2.5"/></svg>
  <div class="event-row">
    <article class="event-card"><h3>Worship &amp;<br>Encounter Night</h3><p class="event-by">Event by<br>Mended, Cherished, Whole</p><div class="event-date"><div class="day">Monday</div><div class="date">DEC 01</div><div class="time">6:30 p.m.</div></div></article>
    <article class="event-card"><h3>Healing Rooms<br>Open</h3><p class="event-by">Event by<br>Mended, Cherished, Whole</p><div class="event-date"><div class="day">Monday</div><div class="date">DEC 15</div><div class="time">6:30 p.m.</div></div></article>
    <article class="event-card"><h3>Teaching &amp; Activation Gathering</h3><p class="event-by">Event by<br>Mended, Cherished, Whole</p><div class="event-date"><div class="day">Sunday</div><div class="date">DEC 14</div><div class="time">6:30 p.m.</div></div></article>
    <article class="event-card"><h3>Lanterns by the River</h3><p class="event-by">Event by<br>Mended, Cherished, Whole</p><div class="event-date"><div class="day">Monday</div><div class="date">DEC 01</div><div class="time">6:30 p.m.</div></div></article>
  </div>
  <svg class="chev" style="left:1092px;top:268px" width="26" height="44" viewBox="0 0 26 44"><path d="M4 2 L22 22 L4 42" fill="none" stroke="#999" stroke-width="2.5"/></svg>
</section>

<section class="invite" role="img" aria-label="Photo of a congregation worshipping with raised hands in a sanctuary">
  <h2 class="abs invite-title">Invitation to Gather</h2>
  <p class="abs invite-copy">You are invited to experience God’s presence with us. Whether in person<br>or online, we believe God has something special for you.</p>
  <div class="btn">View All Events</div>
</section>

<section class="testimonials">
  <h2 class="abs section-title" style="top:48px">Testimonials</h2>
  <div class="abs section-rule" style="top:113px"></div>
  <svg class="chev" style="left:74px;top:261px" width="26" height="44" viewBox="0 0 26 44"><path d="M22 2 L4 22 L22 42" fill="none" stroke="#999" stroke-width="2.5"/></svg>
  <div class="quote-row">
    <article class="quote-card"><p>Experience the Presence of God! The lost are saved. The broken are healed and Jesus is glorified at Mended, Cherished, Whole. Clara and her team love &amp; minister as Jesus said.</p><div class="quote-author"><div class="avatar" role="img" aria-label="Reviewer portrait"></div><div><b>Lauren Hale Whitfield</b><span>12 October</span></div></div></article>
    <article class="quote-card"><p>This is a great place to experience the presence of the Lord! The Holy Spirit is welcome and free to do what needs to be done! Thank you Lord!</p><div class="quote-author"><div class="avatar" role="img" aria-label="Reviewer portrait"></div><div><b>Lauren Hale Whitfield</b><span>12 October</span></div></div></article>
    <article class="quote-card"><p>Experience the Presence of God! The lost are saved. The broken are healed and Jesus is glorified at Mended, Cherished, Whole. Clara and her team love &amp; minister as Jesus said.</p><div class="quote-author"><div class="avatar" role="img" aria-label="Reviewer portrait"></div><div><b>Lauren Hale Whitfield</b><span>12 October</span></div></div></article>
  </div>
  <svg class="chev" style="left:1088px;top:261px" width="26" height="44" viewBox="0 0 26 44"><path d="M4 2 L22 22 L4 42" fill="none" stroke="#999" stroke-width="2.5"/></svg>
</section>

<section class="newsletter">
  <div class="abs newsletter-photo" role="img" aria-label="Photo of a worship gathering under a wooden ceiling with hanging lanterns"></div>
  <h2 class="abs newsletter-title">Join Our Newsletter</h2>
  <p class="abs newsletter-copy">Signup today for free and be the first to get notified on new updates.</p>
  <div class="field" style="left:618px;top:190px;width:209px">First Name</div>
  <div class="field" style="left:840px;top:190px;width:210px">Last Name</div>
  <div class="field" style="left:618px;top:246px;width:432px">Email id</div>
  <div class="btn subscribe">Subscribe</div>
</section>

<footer class="site-footer">
  <div class="brand footer-brand">
    <div class="brand-dot"></div>
    <div class="brand-name">Mended<br>Cherished<br>Whole</div>
  </div>
  <div class="footer-col" style="left:474px">
    <div class="footer-head">MENU</div>
    <ul><li>Home</li><li>About Us</li><li>Meetings &amp; Events</li><li>Encounter</li><li>Healing Rooms</li><li>Live Stream</li></ul>
  </div>
  <div class="footer-col" style="left:645px;width:230px">
    <div class="footer-head">CONTACT US</div>
    <div class="contact-line"><svg width="12" height="16" viewBox="0 0 12 16"><path d="M6 0a6 6 0 0 0-6 6c0 4.5 6 10 6 10s6-5.5 6-10a6 6 0 0 0-6-6zm0 8.2A2.2 2.2 0 1 1 6 3.8a2.2 2.2 0 0 1 0 4.4z" fill="#fff"/></svg><span>4120 W. Meadowlark Lane,<br>Harmony Falls, IL,<br>United States, 60000</span></div>
    <div class="contact-line"><svg width="13" height="13" viewBox="0 0 24 24"><path d="M6.6 10.8a15 15 0 0 0 6.6 6.6l2.2-2.2a1 1 0 0 1 1-.25 11.4 11.4 0 0 0 3.6.57 1 1 0 0 1 1 1V20a1 1 0 0 1-1 1A17 17 0 0 1 3 4a1 1 0 0 1 1-1h3.5a1 1 0 0 1 1 1c0 1.25.2 2.45.57 3.6a1 1 0 0 1-.25 1z" fill="#fff"/></svg><span>+1 555-201-4480</span></div>
    <div class="contact-line"><svg width="13" height="11" viewBox="0 0 13 11"><path d="M0 0h13v11H0z" fill="#fff"/><path d="M0 0l6.5 5.5L13 0" fill="none" stroke="#4b1a80" stroke-width="1.4"/></svg><span>hello@mendedwhole.org</span></div>
  </div>
  <div class="footer-col" style="left:905px">
    <div class="footer-head">FOLLOW US</div>
  </div>
  <div class="footer-social" style="left:904px;top:77px" aria-label="Social profile"></div>
  <div class="footer-social" style="left:947px;top:77px" aria-label="Social profile"></div>
  <div class="footer-social" style="left:988px;top:77px" aria-label="Social profile"></div>
  <div class="abs footer-rule"></div>
  <div class="abs copyright">Copyright © 2025 All Rights Reserved</div>
</footer>

</body>
</html>
```